Personal website for my flying adventures

It is the website for my personal flying adventures.

1. I flew around the world in 2011 and became the first Chinese citizen ever flying the single engine airplane around the world in the history and also the first ever to land the single engine airplane in Halvern Ridge airport.
2. I am organizing the "Copper Kestrels Aerobatic Flying Team" in China
3. I am sharing my flying experiences regularly
4. I am writing the book about flying around the world.

Visit: www.lutanmo.com and www.tanmoskyloop.com for more information and pictures on my flying activities. Need connect two websites together well.

Target Market(s)

Young pilots

Industry/Entity Type

Airport

Requirements
Must have
• Must have the logo of "Tanmo Sky Loop"
• Must have the logo of "Copper Kestrels"
• Must have my flying pictures

```html
<!DOCTYPE html>
<html lang="en">
<head>
<meta charset="utf-8">
<title>Tanmo Sky Loop</title>
<link rel="stylesheet" href="https://fonts.googleapis.com/css2?family=Roboto+Condensed:wght@300;400;700&family=Source+Sans+3:wght@400;600&display=swap">
<style>
:root{
  --red:#d21f2b;
  --blue:#0b9ad6;
  --ink:#1e1e1e;
  --muted:#555;
  --footer:#4a4a4a;
  --footer-dark:#3c3c3c;
  --white:#fff;
  --bubble:rgba(96,84,70,.82);
}
*{margin:0;padding:0;box-sizing:border-box}
html,body{width:1200px;height:1060px;overflow:hidden;background:var(--white)}
body{font-family:"Source Sans 3",Arial,sans-serif;color:var(--ink)}
.page{position:relative;width:1200px;height:1060px;overflow:hidden}

.topbar{position:absolute;left:0;top:0;width:1200px;height:73px;background:var(--white)}
.lang{position:absolute;left:651px;top:26px;font-size:10px;color:#666;display:flex;align-items:center;gap:6px}
.lang-select{display:flex;align-items:center;gap:6px;height:23px;padding:0 8px;border:1px solid #bbb;border-radius:3px;background:linear-gradient(#fff,#e8e8e8);color:#333;font-size:11px}
.lang-flag{width:16px;height:11px;background:#27408b;border:1px solid #999}
.utility-nav{position:absolute;right:181px;top:30px;display:flex;gap:18px;font-size:10px;color:#444}
.utility-nav span.sep{color:#999}

.brand{position:absolute;left:183px;top:0;width:180px;height:133px;background:var(--white);border-radius:0 0 90px 90px;z-index:3;text-align:center}
.brand-mark{display:block;margin:14px auto 0}
.brand-name{font-family:"Roboto Condensed",sans-serif;font-weight:700;font-size:15px;color:var(--blue);margin-top:4px}
.brand-url{font-size:9px;font-weight:600;color:var(--red);margin-top:2px}

.hero{position:absolute;left:0;top:73px;width:1200px;height:502px;background:linear-gradient(180deg,#3a3836 0%,#7a5a3e 22%,#c9743a 40%,#e8a04d 52%,#6b6e78 64%,#3d4450 80%,#5a3a28 100%)}
.main-nav{position:absolute;left:474px;top:94px;display:flex;gap:0;z-index:2;font-size:13.5px;color:var(--white);text-transform:uppercase}
.main-nav a{color:inherit;text-decoration:none;width:145px}
.hero-bubble{position:absolute;left:727px;top:184px;width:288px;height:288px;border-radius:50%;background:var(--bubble);text-align:center;color:#e9e4dc;z-index:2}
.hero-title{font-family:"Roboto Condensed",sans-serif;font-weight:700;font-size:70px;line-height:1;margin-top:56px;letter-spacing:1px}
.hero-sub{font-family:"Roboto Condensed",sans-serif;font-size:31px;line-height:1;margin-top:4px}
.hero-rule{width:206px;height:1px;background:rgba(255,255,255,.35);margin:12px auto 14px}
.hero-text{font-size:9.5px;line-height:19px;width:220px;margin:0 auto;color:var(--white);text-transform:uppercase}
.slider-dots{position:absolute;left:977px;top:552px;display:flex;gap:4px;z-index:2}
.slider-dots i{display:block;width:11px;height:11px;border-radius:50%;background:rgba(255,255,255,.55)}
.slider-dots i:first-child{background:rgba(255,255,255,.9)}

.sponsors{position:absolute;left:0;top:575px;width:1200px;height:141px;border-bottom:2px solid #e1e1e1}
.section-kicker{position:absolute;left:182px;top:19px;font-size:16px;color:var(--red);text-transform:uppercase}
.sponsors-lead{position:absolute;left:182px;top:43px;font-size:10px;font-weight:600;text-transform:uppercase;letter-spacing:-.2px}
.carousel-arrows{position:absolute;left:988px;top:40px;display:flex;gap:3px}
.carousel-arrows span{width:13px;height:13px;background:#bbb;display:flex;align-items:center;justify-content:center}
.sponsor-row{position:absolute;left:182px;top:76px;width:838px;height:50px;display:flex;align-items:center;justify-content:space-between}
.sponsor{display:flex;align-items:center;gap:6px;font-family:"Roboto Condensed",sans-serif;font-weight:700;font-size:16px;color:#2a5fa8}
.sponsor .dot{width:14px;height:14px;border-radius:50%;background:#2a5fa8}

.feature{position:absolute;top:716px;width:262px}
.feature h2{font-family:"Roboto Condensed",sans-serif;font-weight:400;font-size:17px;color:#333;text-transform:uppercase;margin:24px 0 0 2px;height:26px}
.feature-bar{height:5px;background:var(--blue)}
.feature-photo{position:relative;height:108px;margin-top:2px}
.read-more{position:absolute;left:-5px;top:76px;background:var(--red);color:var(--white);font-size:9.5px;padding:5px 14px;text-transform:uppercase}
.feature p{font-size:9.5px;line-height:15.5px;margin:12px 0 0 2px;color:#222}
.feature-about{left:180px}
.feature-media{left:470px}
.feature-expedition{left:758px}
.photo-pilot{background:linear-gradient(160deg,#8fa3b0,#c7c9c6 45%,#6a6e70)}
.photo-engine{background:linear-gradient(160deg,#e8edf2,#9db8d0 50%,#c23030 62%,#6e8ab0)}
.photo-aircraft{background:linear-gradient(170deg,#8d9aa0,#5e7150 55%,#3b4a38)}

.footer{position:absolute;left:0;top:971px;width:1200px;height:89px;background:linear-gradient(var(--footer),var(--footer-dark));color:#ddd}
.itin-icon{position:absolute;left:184px;top:13px;width:66px;height:66px;border-radius:50%;background:radial-gradient(circle at 40% 35%,#f06060,#c4121c 70%)}
.itin-title{position:absolute;left:261px;top:20px;font-family:"Roboto Condensed",sans-serif;font-size:23px;color:#e5e5e5}
.itin-sub{position:absolute;left:261px;top:47px;font-family:"Roboto Condensed",sans-serif;font-size:13px;color:#e5e5e5}
.footer-divider{position:absolute;left:468px;top:14px;width:1px;height:58px;background:#777}
.footer-nav{position:absolute;left:487px;top:30px;display:flex;gap:11px;font-size:8px;text-transform:uppercase;color:#eee}
.footer-nav .sep{color:#aaa}
.copyright{position:absolute;left:487px;top:47px;font-size:8px;text-transform:uppercase;color:#eee}
.social{position:absolute;left:944px;top:32px;display:flex;gap:5px}
.social span{width:22px;height:22px;border-radius:4px;background:#8c8c8c}
</style>
</head>
<body>
<div class="page">

  <header class="topbar">
    <div class="lang">Select Language :
      <span class="lang-select"><span class="lang-flag"></span>English
        <svg width="8" height="6" viewBox="0 0 8 6"><path d="M1 1l3 3 3-3" stroke="#333" stroke-width="1.6" fill="none"/></svg>
      </span>
    </div>
    <nav class="utility-nav"><span>HOME</span><span class="sep">|</span><span>CONTESTS</span><span class="sep">|</span><span>STORE</span></nav>
  </header>

  <div class="brand">
    <svg class="brand-mark" width="58" height="58" viewBox="0 0 58 58"><circle cx="29" cy="29" r="27" fill="var(--blue)"/></svg>
    <div class="brand-name">Tanmo Sky Loop</div>
    <div class="brand-url">WWW.LUTANMO.COM</div>
  </div>

  <section class="hero" role="img" aria-label="Business jet parked on a wet runway at sunset">
  </section>
  <nav class="main-nav">
    <a>The Expedition</a><a>Media Room</a><a>Sponsors</a><a>Tanmo Tracker</a>
  </nav>
  <div class="hero-bubble">
    <div class="hero-title">TANMO</div>
    <div class="hero-sub">SKY LOOP</div>
    <div class="hero-rule"></div>
    <div class="hero-text">Welcome to the online media room for Tanmo Sky Loop where you can find press releases and other news</div>
  </div>
  <div class="slider-dots"><i></i><i></i><i></i></div>

  <section class="sponsors">
    <h2 class="section-kicker">Sponcers</h2>
    <p class="sponsors-lead">Global sponsorship opportunities available intended to touch the hearts and minds of over 1.3 billion Chinese.</p>
    <div class="carousel-arrows">
      <span><svg width="6" height="8" viewBox="0 0 6 8"><path d="M5 1L2 4l3 3" stroke="#fff" stroke-width="1.5" fill="none"/></svg></span>
      <span><svg width="6" height="8" viewBox="0 0 6 8"><path d="M1 1l3 3-3 3" stroke="#fff" stroke-width="1.5" fill="none"/></svg></span>
    </div>
    <div class="sponsor-row">
      <div class="sponsor"><span class="dot"></span>Lantern Net</div>
      <div class="sponsor" style="color:var(--red)">Riverbell Daily</div>
      <div class="sponsor">Kitepost</div>
      <div class="sponsor" style="color:#1d3f8a">Orrin Aero Parts</div>
      <div class="sponsor" style="color:#333">The Marlowe Hotel</div>
      <div class="sponsor"><span class="dot"></span>Delta Bay Chamber</div>
    </div>
  </section>

  <article class="feature feature-about">
    <h2>About Tanmo Sky Loop</h2>
    <div class="feature-bar"></div>
    <div class="feature-photo photo-pilot" role="img" aria-label="Pilot in uniform standing beside a single engine airplane"><span class="read-more">Read More</span></div>
    <p>Welcome to the Online Media Room for Tanmo Sky Loop where you can find press releases and other news:<br>Ash blocks Tanmo's way: Memphis aviator stuck in Canada</p>
  </article>
  <article class="feature feature-media">
    <h2>Media Room</h2>
    <div class="feature-bar"></div>
    <div class="feature-photo photo-engine" role="img" aria-label="Close view of a jet engine in flight above clouds"><span class="read-more">Read More</span></div>
    <p>Welcome to the Online Media Room for Tanmo Sky Loop where you can find press releases and other news:<br>Ash blocks Tanmo's way: Memphis aviator stuck in Canada</p>
  </article>
  <article class="feature feature-expedition">
    <h2>The Expedition</h2>
    <div class="feature-bar"></div>
    <div class="feature-photo photo-aircraft" role="img" aria-label="Business jet flying over forested hills"><span class="read-more">Read More</span></div>
    <p>Welcome to the Online Media Room for Tanmo Sky Loop where you can find press releases and other news:<br>Ash blocks Tanmo's way: Memphis aviator stuck in Canada</p>
  </article>

  <footer class="footer">
    <div class="itin-icon"></div>
    <div class="itin-title">FLIGHT ITINERARY</div>
    <div class="itin-sub">DOWNLOAD LATEST FLIGHT ITINERARY</div>
    <div class="footer-divider"></div>
    <nav class="footer-nav">
      <span>Home</span><span class="sep">|</span><span>The Expedition</span><span class="sep">|</span><span>Media Room</span><span class="sep">|</span><span>Sponsors</span><span class="sep">|</span><span>Tanmo Tracker</span><span class="sep">|</span><span>Contests</span><span class="sep">|</span><span>Store</span>
    </nav>
    <div class="copyright">Copyright © 2013 Tanmo Sky Loop. All rights reserved.</div>
    <div class="social" aria-label="Social links"><span title="Chirpline"></span><span title="Friendwall"></span><span title="ReelTube"></span></div>
  </footer>

</div>
</body>
</html>
```